Designer Instructions – Updated Referral Program Flyer

(Based on the mock-up in “Brief Layout and Instructions.pdf”)

OVERALL STYLE + LAYOUT

Maintain the same general layout, structure, and flow as the mock-up flyer (front and back).

This is an update of an older flyer, not a full redesign — keep the same sections, proportions, and overall visual feel, but with cleaner, more modern design improvements.

The final flyer should look clean, bold, professional, and high-impact, geared toward realtors, property managers, and contractors who refer work.

FRONT SIDE INSTRUCTIONS
1. Header Section

Remove the Rebuild Harbor Crest logo from the top banner.
(Shown on page 1 of the PDF)

2. Main Headline

Keep the same three-line structure:
EARN
UNLIMITED
CASH

Center it, maximize impact, and increase the font size of CASH so all three words match in importance.

Make the headline bold, clean, and the main focal point.

3. Cash Incentive Box

Keep the "$500 minimum OR 10% per referral" box, but upgrade the graphics to look sharper and more modern.

Ensure the wording matches exactly what’s in the mock-up.

4. Premier Partner Program Ribbon

Clean up and modernize the "PREMIER PARTNER PROGRAM" bar while keeping the same position and structure.

Ensure the checkmark badge remains crisp and professional.

5. Supporting Icons Section

Keep the four icons/benefit boxes (Guaranteed Payout, Free Evaluations, Affordable Solutions, Industry Leaders) in the same order.

Update the icons to cleaner, more modern styles — but maintain the same meanings.

Improve alignment and spacing for sharper visual consistency.

6. Remove Icons in Contact Area

At the bottom (“CALL TEXT OR BOOK ONLINE 858-471-6093 BrightlaneRenovate.com”), remove the phone and internet icons, as noted on page 2 of the PDF.

7. Replace All Images

I (Dorian) will provide all updated stock images separately via email.

Replace the flood/water-damage imagery and roof leak with the new images I send.

Keep image placement and proportions the same as the mock-up.

BACK SIDE INSTRUCTIONS
1. Header Image + “REFER / EARN” Section

Maintain the same large split-image layout (“The more you refer, the more you earn”).

Replace all background imagery with the new assets I will send.

Keep the CASH FLOW image section but modernize the type and spacing.

2. “HOW IT WORKS” Section

Preserve the three-column layout:

Refer Flood, Water & Mold Damage

We Take Care of Everything (evaluations/insurance)

Get Paid to Share

Update images, tighten spacing, and use modern iconography.

3. Remove Phone/Internet Icons

Same as the front side — remove small communication icons and keep only the text/number/URL.

4. Bottom Contact Bar

Keep the blue bar, same wording, same layout — just modernize the style if needed for clarity.

5. Replace All Back-Side Images

Again, I will email you the image assets.

Keep the layout EXACT — just update with higher-quality photos and improved design.

TEXT CONTENT (Keep as-is unless spacing adjustments needed)

All text shown in the PDF should remain exactly the same unless spacing or visual balance requires minor adjustments.
Example from page 3:

“REFER FLOOD, MOLD & CONSTRUCTION JOBS”

“We Schedule a Free Estimate. If Approved, You Get Paid.”

“Everybody Benefits From Referrals”

Everything stays, just refreshed and visually improved.

DESIGN GOALS

Flyer should look high-end and trustworthy, not salesy.

Consistent color theme: blues, whites, yellows, same palette as original.

Use bold, modern fonts with strong readability.

Ensure all headlines pop and all benefit boxes are clean, well-aligned, and evenly spaced.

The final result should feel like a premium referral program flyer for a top-tier restoration/remodel company.

FILES I WILL PROVIDE

I will send the designer:

All replacement stock photos

Any updated logos (if needed)

Original high-resolution version of the mock-up (if available)

Any additional icons preferred

Colors
0054AA
0677BA
7BADD7
CADEEF
E8F1F8

Requirements
Must have
• Designer Instructions – Updated Referral Program Flyer (Based on the mock-up in “Brief Layout and Instructions.pdf”) OVERALL STYLE + LAYOUT Maintain the same general layout, structure, and flow as the mock-up flyer (front and back). This is an update of an older flyer, not a full redesign — keep the same sections, proportions, and overall visual feel, but with cleaner, more modern design improvements. The final flyer should look clean, bold, professional, and high-impact, geared toward realtors, property managers, and contractors who refer work. FRONT SIDE INSTRUCTIONS 1. Header Section Remove the Rebuild Harbor Crest logo from the top banner. (Shown on page 1 of the PDF) 2. Main Headline Keep the same three-line structure: EARN UNLIMITED CASH Center it, maximize impact, and increase the font size of CASH so all three words match in importance. Make the headline bold, clean, and the main focal point. 3. Cash Incentive Box Keep the "$500 minimum OR 10% per referral" box, but upgrade the graphics to look sharper and more modern. Ensure the wording matches exactly what’s in the mock-up. 4. Premier Partner Program Ribbon Clean up and modernize the "PREMIER PARTNER PROGRAM" bar while keeping the same position and structure. Ensure the checkmark badge remains crisp and professional. 5. Supporting Icons Section Keep the four icons/benefit boxes (Guaranteed Payout, Free Evaluations, Affordable Solutions, Industry Leaders) in the same order. Update the icons to cleaner, more modern styles — but maintain the same meanings. Improve alignment and spacing for sharper visual consistency. 6. Remove Icons in Contact Area At the bottom (“CALL TEXT OR BOOK ONLINE 858-471-6093 BrightlaneRenovate.com”), remove the phone and internet icons, as noted on page 2 of the PDF. 7. Replace All Images I (Dorian) will provide all updated stock images separately via email. Replace the flood/water-damage imagery and roof leak with the new images I send. Keep image placement and proportions the same as the mock-up. BACK SIDE INSTRUCTIONS 1. Header Image + “REFER / EARN” Section Maintain the same large split-image layout (“The more you refer, the more you earn”). Replace all background imagery with the new assets I will send. Keep the CASH FLOW image section but modernize the type and spacing. 2. “HOW IT WORKS” Section Preserve the three-column layout: Refer Flood, Water & Mold Damage We Take Care of Everything (evaluations/insurance) Get Paid to Share Update images, tighten spacing, and use modern iconography. 3. Remove Phone/Internet Icons Same as the front side — remove small communication icons and keep only the text/number/URL. 4. Bottom Contact Bar Keep the blue bar, same wording, same layout — just modernize the style if needed for clarity. 5. Replace All Back-Side Images Again, I will email you the image assets. Keep the layout EXACT — just update with higher-quality photos and improved design. TEXT CONTENT (Keep as-is unless spacing adjustments needed) All text shown in the PDF should remain exactly the same unless spacing or visual balance requires minor adjustments. Example from page 3: “REFER FLOOD, MOLD & CONSTRUCTION JOBS” “We Schedule a Free Estimate. If Approved, You Get Paid.” “Everybody Benefits From Referrals” Everything stays, just refreshed and visually improved. DESIGN GOALS Flyer should look high-end and trustworthy, not salesy. Consistent color theme: blues, whites, yellows, same palette as original. Use bold, modern fonts with strong readability. Ensure all headlines pop and all benefit boxes are clean, well-aligned, and evenly spaced. The final result should feel like a premium referral program flyer for a top-tier restoration/remodel company. FILES I WILL PROVIDE I will send the designer: All replacement stock photos Any updated logos (if needed) Original high-resolution version of the mock-up (if available) Any additional icons preferred

```html
<!DOCTYPE html>
<html lang="en">
<head>
<meta charset="utf-8">
<title>Referral Program Flyer – Front and Back</title>
<link href="https://fonts.googleapis.com/css2?family=Poppins:wght@400;500;600;700;800;900&display=swap" rel="stylesheet">
<style>
  :root{
    --page:#e9e9ea;
    --blue:#1d4c9c;
    --blue-deep:#163c84;
    --navy:#13306b;
    --ink:#122a63;
    --yellow:#ffe000;
    --orange:#ff9a00;
    --red:#e91d27;
    --slate:#7b8f9b;
    --white:#ffffff;
    --sky:#cadeef;
    --mist:#e8f1f8;
  }
  *{box-sizing:border-box;margin:0;padding:0}
  html,body{width:1200px;height:1200px;overflow:hidden}
  body{background:var(--page);font-family:'Poppins',sans-serif;color:var(--ink);position:relative}
  .card{position:absolute;left:237px;width:727px;height:470px;background:var(--white);overflow:hidden;box-shadow:0 6px 16px rgba(0,0,0,.14)}
  .card--front{top:114px}
  .card--back{top:617px}
  .abs{position:absolute}
  .header-art{position:absolute;left:0;top:0}
  .headline{position:absolute;text-align:center;font-weight:800;line-height:.92;text-transform:uppercase}
  .gold{background:linear-gradient(180deg,var(--yellow) 35%,var(--orange));-webkit-background-clip:text;background-clip:text;color:transparent}
  .white{color:var(--white)}
  .banner-text{position:absolute;font-weight:700;color:var(--ink);text-transform:uppercase;letter-spacing:.2px}

  /* incentive */
  .incentive{position:absolute;left:21px;top:254px;height:42px;width:331px}
  .incentive__box{position:absolute;top:0;height:42px;background:var(--red);border-radius:4px;color:var(--white);font-weight:800;display:flex;align-items:center}
  .incentive__min{left:0;width:110px;flex-direction:column;justify-content:center;line-height:1}
  .incentive__min b{font-size:22px;font-weight:800}
  .incentive__min b sup{font-size:11px;vertical-align:top;position:relative;top:2px}
  .incentive__min span{font-size:10px;font-weight:700}
  .incentive__pct{left:127px;width:204px;padding-left:26px;gap:8px}
  .incentive__pct b{font-size:34px;line-height:1;letter-spacing:-1px}
  .incentive__pct span{font-size:14px;line-height:1.05;font-weight:700}
  .incentive__or{position:absolute;left:99px;top:5px;width:33px;height:33px;border-radius:50%;background:#f1f1f1;border:3px solid var(--white);display:flex;align-items:center;justify-content:center;font-weight:800;font-size:13px;color:var(--ink);z-index:2}

  /* premier ribbon */
  .premier{position:absolute;left:373px;top:253px;width:332px}
  .premier__kicker{text-align:center;color:var(--red);font-size:11px;font-weight:500;letter-spacing:10px;margin-left:8px;line-height:1}
  .premier__bar{margin-top:4px;height:29px;border-radius:4px;overflow:hidden;display:flex;position:relative}
  .premier__half{flex:1;display:flex;align-items:center;justify-content:center;color:var(--white);font-weight:700;font-size:14px;letter-spacing:4px}
  .premier__half--red{background:var(--red);padding-right:20px}
  .premier__half--grey{background:var(--slate);padding-left:20px}
  .premier__badge{position:absolute;left:50%;top:1px;transform:translateX(-50%)}

  /* benefits */
  .pitch{position:absolute;left:21px;top:323px;width:100px;font-size:15px;line-height:.98;font-weight:800;color:var(--navy);text-transform:uppercase;padding-bottom:4px;border-bottom:1.5px solid var(--blue)}
  .benefit{position:absolute;top:315px;width:107px;height:73px;border:1.5px solid var(--blue);border-top:none;border-radius:0 0 6px 6px}
  .benefit__title{position:absolute;left:-1px;top:-1px;width:107px;height:30px;border:2px solid var(--blue);border-radius:14px;background:var(--white);font-size:9.5px;line-height:1.05;font-weight:700;color:var(--navy);text-align:center;display:flex;align-items:center;justify-content:center;text-transform:uppercase}
  .benefit__text{position:absolute;left:8px;top:40px;width:70px;font-size:6.4px;line-height:1.3;font-weight:500;color:var(--navy)}
  .benefit__icon{position:absolute;right:-6px;top:40px}

  .tagline{position:absolute;left:0;width:100%;top:400px;text-align:center;font-size:19.5px;font-weight:800;color:var(--navy);text-transform:uppercase}
  .tagline em{font-style:normal;color:var(--red)}

  /* contact bar */
  .contact{position:absolute;left:0;bottom:0;width:100%;height:34px}
  .contact__cta{position:absolute;left:44px;top:0;height:34px;display:flex;align-items:center;color:var(--white);font-weight:700;font-size:15px;text-transform:uppercase}
  .contact__info{position:absolute;left:363px;top:0;height:32px;display:flex;align-items:center;gap:12px;color:#111}
  .contact__phone{font-weight:800;font-size:16px;letter-spacing:.3px}
  .contact__sep{width:1px;height:16px;background:#222}
  .contact__url{font-weight:500;font-size:11.5px;letter-spacing:.4px}

  /* back: refer list */
  .refer-list{position:absolute;left:21px;top:294px;font-size:15px;line-height:.98;font-weight:800;text-transform:uppercase;color:var(--navy)}
  .refer-list .lead{color:var(--red)}
  .step{position:absolute;top:243px;width:168px;height:173px;border:1.5px solid var(--blue);border-radius:7px;overflow:hidden;text-align:center}
  .step__photo{display:block;width:100%;height:88px;border-bottom:1.5px solid var(--blue)}
  .step__title{margin-top:12px;font-size:10.8px;line-height:1.1;font-weight:800;color:var(--navy);text-transform:uppercase;padding:0 6px}
  .step__text{margin-top:8px;font-size:8.6px;line-height:1.3;font-weight:500;color:#111;padding:0 6px}
  .step__text span{color:var(--blue)}
</style>
</head>
<body>

<!-- FRONT -->
<section class="card card--front" aria-label="Referral program flyer front">
  <svg class="header-art" width="727" height="235" viewBox="0 0 727 235" aria-hidden="true">
    <defs>
      <linearGradient id="kitchenTone" x1="0" y1="0" x2="0" y2="1">
        <stop offset="0" stop-color="#cfdbe4"/><stop offset=".6" stop-color="#9fb7c9"/><stop offset="1" stop-color="#5c6670"/>
      </linearGradient>
      <linearGradient id="moneyTone" x1="0" y1="0" x2="1" y2="1">
        <stop offset="0" stop-color="#2a57a8"/><stop offset="1" stop-color="#1c478f"/>
      </linearGradient>
    </defs>
    <rect width="727" height="235" fill="url(#moneyTone)"/>
    <polygon points="40,0 250,0 420,235 160,235" fill="#13306b" opacity=".55"/>
  </svg>
  <svg class="abs" style="left:0;top:0" width="727" height="235" viewBox="0 0 727 235" role="img" aria-label="Photo of a bright white kitchen with water pouring from a hole in the ceiling onto the island">
    <polygon points="412,0 727,0 727,235 412,235 368,119" fill="url(#kitchenTone)" stroke="#ffffff" stroke-width="4"/>
  </svg>

  <div class="headline" style="left:33px;top:26px;width:280px">
    <div class="gold" style="font-size:54px">Earn</div>
    <div class="white" style="font-size:39px;margin-top:2px">Unlimited</div>
    <div class="gold" style="font-size:54px;margin-top:2px">Cash</div>
  </div>

  <svg class="abs" style="left:0;top:192px" width="440" height="33" viewBox="0 0 440 33" aria-hidden="true">
    <polygon points="0,0 418,0 430,33 0,33" fill="var(--yellow)"/>
  </svg>
  <div class="banner-text" style="left:24px;top:193px;font-size:21px;line-height:31px">Get Paid to Refer a Flood</div>

  <div class="incentive">
    <div class="incentive__box incentive__min"><b><sup>$</sup>500</b><span>MINIMUM</span></div>
    <div class="incentive__or">OR</div>
    <div class="incentive__box incentive__pct"><b>10%</b><span>PER<br>REFERRAL</span></div>
  </div>

  <div class="premier">
    <div class="premier__kicker">PREMIER</div>
    <div class="premier__bar">
      <div class="premier__half premier__half--red">PARTNER</div>
      <div class="premier__half premier__half--grey">PROGRAM</div>
      <svg class="premier__badge" width="24" height="27" viewBox="0 0 24 27" aria-hidden="true">
        <path d="M12 1 L22 5 V13 C22 19 17 23.5 12 26 C7 23.5 2 19 2 13 V5 Z" fill="#fff" stroke="var(--red)" stroke-width="1.5"/>
        <path d="M7 13 L11 17 L17.5 9.5" fill="none" stroke="var(--red)" stroke-width="2.6" stroke-linecap="round" stroke-linejoin="round"/>
      </svg>
    </div>
  </div>

  <div class="pitch">Partner with us &amp; everybody wins!</div>

  <div class="benefit" style="left:174px">
    <div class="benefit__title">Guaranteed<br>Payout</div>
    <div class="benefit__text">Minimum $500 or 10% of Total Invoice Paid Fast</div>
    <svg class="benefit__icon" width="24" height="24" viewBox="0 0 24 24" aria-hidden="true" fill="none" stroke="#1a1a1a" stroke-width="1.2">
      <path d="M12 1.5l2.6 1.9 3.2-.2.9 3.1 2.6 1.9-1.2 3 1.2 3-2.6 1.9-.9 3.1-3.2-.2L12 22.5 9.4 20.6l-3.2.2-.9-3.1-2.6-1.9 1.2-3-1.2-3 2.6-1.9.9-3.1 3.2.2z" fill="#fff"/>
      <circle cx="12" cy="12" r="5.5"/><path d="M9.5 12l1.8 1.8L14.8 10"/>
    </svg>
  </div>
  <div class="benefit" style="left:313px">
    <div class="benefit__title">Free<br>Estimates</div>
    <div class="benefit__text" style="top:44px;width:78px">Fast &amp; Free Inspections &amp; Written Estimates</div>
    <svg class="benefit__icon" width="24" height="24" viewBox="0 0 24 24" aria-hidden="true" fill="#fff" stroke="#1a1a1a" stroke-width="1.2">
      <rect x="4" y="3.5" width="14" height="18" rx="1.5"/><rect x="8" y="2" width="6" height="3" rx="1"/>
      <path d="M7 9h8M7 12h8M7 15h5" fill="none"/><path d="M15 16l2 2 4-5" fill="none"/>
    </svg>
  </div>
  <div class="benefit" style="left:452px">
    <div class="benefit__title">Affordable<br>Solutions</div>
    <div class="benefit__text">Lowest Out of Pocket Costs for Your Customers</div>
    <svg class="benefit__icon" width="24" height="24" viewBox="0 0 24 24" aria-hidden="true" fill="none" stroke="#1a1a1a" stroke-width="1.2">
      <circle cx="13" cy="9" r="6" fill="#fff"/><path d="M13 5.5v7M15 7c-.6-.8-4-.9-4 .7 0 1.8 4 .9 4 2.7 0 1.5-3.4 1.4-4 .6"/>
      <path d="M2 17h4l3 2h5l6-4M6 21H2"/>
    </svg>
  </div>
  <div class="benefit" style="left:591px">
    <div class="benefit__title">Industry<br>Leaders</div>
    <div class="benefit__text">Licensed &amp; Certified Experts Provide 100% Guarantee</div>
    <svg class="benefit__icon" width="24" height="24" viewBox="0 0 24 24" aria-hidden="true" fill="none" stroke="#1a1a1a" stroke-width="1.2">
      <circle cx="12" cy="6" r="3.5"/><path d="M12 4.5v3M10.5 6h3"/>
      <circle cx="5" cy="15" r="2"/><circle cx="12" cy="15" r="2"/><circle cx="19" cy="15" r="2"/>
      <path d="M2 22c0-2.5 6-2.5 6 0M9 22c0-2.5 6-2.5 6 0M16 22c0-2.5 6-2.5 6 0M12 10v3M8 11l-2 2M16 11l2 2"/>
    </svg>
  </div>

  <div class="tagline">Send <em>Referrals</em>. Get <em>Paid</em>. Grow <em>Your Business.</em></div>

  <div class="contact">
    <svg class="abs" style="left:0;top:0" width="727" height="34" viewBox="0 0 727 34" aria-hidden="true">
      <polygon points="0,0 310,0 328,34 0,34" fill="var(--blue)"/>
      <rect x="332" y="31" width="395" height="3" fill="var(--yellow)"/>
    </svg>
    <div class="contact__cta">Call, Text or Book Online</div>
    <div class="contact__info"><span class="contact__phone">858-471-6093</span><span class="contact__sep"></span><span class="contact__url">www.BrightlaneRenovate.com</span></div>
  </div>
</section>

<!-- BACK -->
<section class="card card--back" aria-label="Referral program flyer back">
  <svg class="header-art" width="727" height="209" viewBox="0 0 727 209" aria-hidden="true">
    <defs>
      <linearGradient id="skylineTone" x1="0" y1="0" x2="0" y2="1">
        <stop offset="0" stop-color="#1f4f9f"/><stop offset="1" stop-color="#1a4690"/>
      </linearGradient>
      <linearGradient id="cashTone" x1="0" y1="0" x2="1" y2="1">
        <stop offset="0" stop-color="#e6e8e2"/><stop offset=".5" stop-color="#c7ccc4"/><stop offset="1" stop-color="#a9b0a8"/>
      </linearGradient>
    </defs>
    <rect width="727" height="209" fill="url(#skylineTone)"/>
    <polygon points="40,0 240,0 330,209 130,209" fill="#13306b" opacity=".55"/>
  </svg>
  <svg class="abs" style="left:0;top:0" width="727" height="209" viewBox="0 0 727 209" role="img" aria-label="Photo of scattered hundred dollar bills with letter tiles spelling CASH FLOW">
    <polygon points="325,0 727,0 727,209 408,209" fill="url(#cashTone)" stroke="#ffffff" stroke-width="4"/>
  </svg>

  <div class="headline" style="left:44px;top:26px;width:220px">
    <div class="white" style="font-size:22px">The more you</div>
    <div class="gold" style="font-size:49px;margin-top:1px">Refer</div>
    <div class="white" style="font-size:22px;margin-top:1px">The more you</div>
    <div class="gold" style="font-size:56px;margin-top:1px">Earn</div>
  </div>

  <svg class="abs" style="left:0;top:190px" width="320" height="33" viewBox="0 0 320 33" aria-hidden="true">
    <polygon points="0,0 293,0 306,33 0,33" fill="var(--yellow)"/>
  </svg>
  <div class="banner-text" style="left:69px;top:191px;font-size:21px;line-height:31px">How it works</div>

  <div class="refer-list"><span class="lead">Refer:</span><br>Floods,<br>Remodels,<br>Renovations<br>&amp; Repairs</div>

  <div class="step" style="left:164px">
    <svg class="step__photo" viewBox="0 0 168 88" preserveAspectRatio="none" role="img" aria-label="Photo of blue drying fans and dehumidifiers in a water-damaged room"><rect width="168" height="88" fill="#a7b4ba"/></svg>
    <div class="step__title">Refer Flood, Mold &amp;<br>Construction Jobs</div>
    <div class="step__text">It’s Simple to Refer 24/7:<br><span>Call, Text or Book Online.</span></div>
  </div>
  <div class="step" style="left:350px">
    <svg class="step__photo" viewBox="0 0 168 88" preserveAspectRatio="none" role="img" aria-label="Photo of an inspector holding a clipboard in front of a house"><rect width="168" height="88" fill="#b9c2b8"/></svg>
    <div class="step__title">We Take Care of<br>Everything</div>
    <div class="step__text">We Schedule a Free Estimate.<br><span>If Approved,</span> You Get Paid.</div>
  </div>
  <div class="step" style="left:537px">
    <svg class="step__photo" viewBox="0 0 168 88" preserveAspectRatio="none" role="img" aria-label="Photo of a yellow road sign reading Get Paid to Share against a blue sky"><rect width="168" height="88" fill="#7badd7"/></svg>
    <div class="step__title">Everybody Benefits<br>From Referrals</div>
    <div class="step__text">We Provide <span>Expert Quality</span><br>Work for Affordable Price.</div>
  </div>

  <div class="contact">
    <svg class="abs" style="left:0;top:0" width="727" height="34" viewBox="0 0 727 34" aria-hidden="true">
      <polygon points="0,0 310,0 328,34 0,34" fill="var(--blue)"/>
      <rect x="332" y="31" width="395" height="3" fill="var(--yellow)"/>
    </svg>
    <div class="contact__cta">Call, Text or Book Online</div>
    <div class="contact__info"><span class="contact__phone">858-471-6093</span><span class="contact__sep"></span><span class="contact__url">www.BrightlaneRenovate.com</span></div>
  </div>
</section>

</body>
</html>
```